Mist Humidifier Packaging Design

I want to design a packaging for our product which is an Ultrasonic Cool Mist Humidifier. Please use the Manual and images I give to you to finish this design. Please DO NOT COPY From the sample, we need brilliant ideas for this design
Full description of the product is in its manual I attached. People use humidifiers in dry or frozen areas where the air is dry.
It has a remote control & a digital screen to show the humidity percentage of the room

Target Market(s)

We want to sell this product in USA market on Vendiqo.com & on shelf

Industry/Entity Type

Home Improvement

Font styles to use
Serif

Colors
e34096
faa54b
ecf7fb
33a6d7

Requirements
Must have
• It should have bullet points of the features of the product
• BRT Certificate & other related icons
• Brief description of the product from Manual
• in use design (in application)
Nice to have
• Babies room or Living room image
• Laugh and happy family maybe
• Icons

```html
<!DOCTYPE html>
<html lang="en">
<head>
<meta charset="utf-8">
<title>Ultrasonic Cool Mist Humidifier – Packaging</title>
<link href="https://fonts.googleapis.com/css2?family=PT+Sans:wght@400;700&family=PT+Sans+Narrow:wght@400;700&display=swap" rel="stylesheet">
<style>
  :root{
    --pink:#e34096;
    --orange:#faa54b;
    --orange-deep:#e9852f;
    --ice:#ecf7fb;
    --blue:#33a6d7;
    --blue-deep:#1f8fc4;
    --white:#ffffff;
    --stage:#e6e6e6;
  }
  *{box-sizing:border-box;margin:0;padding:0}
  html,body{width:1182px;height:1200px;overflow:hidden;background:var(--stage)}
  body{font-family:"PT Sans",Arial,sans-serif;position:relative}

  .panel{position:absolute;top:70px;height:1060px;overflow:hidden}
  .front{left:40px;width:700px;background:var(--orange-deep)}
  .side{left:760px;width:382px;background:var(--orange)}

  /* FRONT */
  .title-band{position:absolute;left:0;top:0;width:100%;height:190px;background:var(--blue)}
  .title-band .wave{position:absolute;left:0;bottom:-40px;width:100%;height:80px}
  .subtitle{position:absolute;left:0;top:56px;width:100%;height:48px;background:var(--pink);
    color:var(--white);font-weight:700;font-size:38px;line-height:48px;padding-left:30px}
  .main-title{position:absolute;left:30px;top:104px;color:var(--white);font-weight:700;
    font-size:66px;letter-spacing:2px;line-height:76px}

  .lifestyle-photo{position:absolute;left:280px;top:150px;width:420px;height:800px;
    background:linear-gradient(160deg,#f4f1ec 0%,#e8ddd4 45%,#d9c6b8 100%)}

  .features{position:absolute;left:30px;top:245px;width:250px;list-style:none;color:var(--white);
    font-family:"PT Sans Narrow","PT Sans",sans-serif;font-size:21px;line-height:23px}
  .features li{position:relative;padding-left:16px;margin-bottom:10px}
  .features li::before{content:"";position:absolute;left:0;top:8px;width:8px;height:8px;border-radius:50%;background:var(--blue)}

  .product-shot{position:absolute;left:40px;top:560px;width:300px;height:340px;
    background:linear-gradient(180deg,#f2f2f2,#c9cbcd);border-radius:30px 30px 10px 10px}

  .icon-row{position:absolute;left:175px;top:940px;display:flex;gap:14px}
  .icon-row svg{width:58px;height:58px}

  .cert{position:absolute;left:30px;top:990px;color:var(--white);font-size:32px;font-weight:700}

  /* SIDE */
  .benefit-band{position:absolute;left:0;top:0;width:100%;height:300px;background:var(--blue)}
  .benefit-title{margin:40px auto 16px;width:250px;background:var(--pink);color:var(--white);
    text-align:center;font-weight:700;font-size:20px;line-height:30px}
  .benefit-list{list-style:decimal;color:var(--white);font-size:13px;line-height:17px;padding:0 34px 0 52px}
  .benefit-list li{margin-bottom:8px}
  .side-photo{position:absolute;left:0;top:300px;width:150px;height:760px;
    background:linear-gradient(180deg,#f1ede8,#dcd0c6)}
  .perks{position:absolute;left:165px;top:330px;list-style:none;width:200px}
  .perks li{display:flex;flex-direction:column;align-items:center;margin-bottom:18px}
  .perks svg{width:44px;height:44px;margin-bottom:6px}
  .perks span{background:var(--blue);color:var(--white);font-family:"PT Sans Narrow",sans-serif;
    font-size:17px;line-height:20px;padding:5px 10px;text-align:center;width:100%}
</style>
</head>
<body>

<section class="panel front">
  <div class="lifestyle-photo" role="img" aria-label="Happy family of three sitting together in a bright living room"></div>

  <header class="title-band">
    <svg class="wave" viewBox="0 0 700 80" preserveAspectRatio="none"><path d="M0 0 H700 V40 Q350 80 0 40 Z" fill="#33a6d7"/></svg>
    <div class="subtitle">Ultrasonic Cool Mist</div>
    <h1 class="main-title">HUMIDIFIER</h1>
  </header>

  <ul class="features">
    <li>Provides clean &amp; fresh air</li>
    <li>Help you breathe better</li>
    <li>Prevent &amp; relieves cough, could, flu symptoms, sinus irritation, and dry skin</li>
    <li>Creates calming &amp; conforting atmosphere</li>
  </ul>

  <div class="product-shot" role="img" aria-label="White ultrasonic humidifier with digital humidity display and remote control"></div>

  <div class="icon-row">
    <svg viewBox="0 0 58 58"><circle cx="29" cy="29" r="27" fill="#fff"/><circle cx="29" cy="29" r="23" fill="#e34096"/><path d="M22 22a10 10 0 1 0 14 0" stroke="#fff" stroke-width="3" fill="none"/><line x1="29" y1="17" x2="29" y2="29" stroke="#fff" stroke-width="3"/></svg>
    <svg viewBox="0 0 58 58"><circle cx="29" cy="29" r="27" fill="#fff"/><circle cx="29" cy="29" r="23" fill="#e34096"/><circle cx="29" cy="29" r="12" stroke="#fff" stroke-width="2" fill="none"/><text x="29" y="35" text-anchor="middle" fill="#fff" font-size="16" font-weight="700" font-family="PT Sans,sans-serif">A</text></svg>
    <svg viewBox="0 0 58 58"><circle cx="29" cy="29" r="27" fill="#fff"/><circle cx="29" cy="29" r="23" fill="#e34096"/><g stroke="#fff" stroke-width="2.5"><line x1="29" y1="16" x2="29" y2="42"/><line x1="18" y1="22" x2="40" y2="36"/><line x1="18" y1="36" x2="40" y2="22"/></g></svg>
    <svg viewBox="0 0 58 58"><circle cx="29" cy="29" r="27" fill="#fff"/><circle cx="29" cy="29" r="23" fill="#e34096"/><rect x="23" y="20" width="12" height="22" rx="2" fill="#fff"/><path d="M22 15q7-5 14 0" stroke="#fff" stroke-width="2" fill="none"/></svg>
    <svg viewBox="0 0 58 58"><circle cx="29" cy="29" r="27" fill="#fff"/><circle cx="29" cy="29" r="23" fill="#e34096"/><text x="29" y="28" text-anchor="middle" fill="#fff" font-size="13" font-weight="700" font-family="PT Sans,sans-serif">360°</text><path d="M17 33q12 10 24 0" stroke="#fff" stroke-width="2" fill="none"/></svg>
    <svg viewBox="0 0 58 58"><circle cx="29" cy="29" r="27" fill="#fff"/><circle cx="29" cy="29" r="23" fill="#e34096"/><text x="29" y="28" text-anchor="middle" fill="#fff" font-size="14" font-weight="700" font-family="PT Sans,sans-serif">12h</text><path d="M17 34q6-4 12 0t12 0M17 40q6-4 12 0t12 0" stroke="#fff" stroke-width="2" fill="none"/></svg>
  </div>

  <div class="cert">BRT</div>
</section>

<aside class="panel side">
  <div class="benefit-band">
    <h2 class="benefit-title">Benefit</h2>
    <ol class="benefit-list">
      <li>Ultrasonic mist adds gentle moisture to dry room air.</li>
      <li>Quiet operation lets the whole family sleep soundly.</li>
      <li>Digital display shows room humidity at a glance.</li>
      <li>Auto shut-off stops the unit when water runs low.</li>
      <li>Easy-fill tank and simple cleaning for daily use.</li>
    </ol>
  </div>

  <div class="side-photo" role="img" aria-label="Humidifier in use beside a houseplant in a living room"></div>

  <ul class="perks">
    <li><svg viewBox="0 0 44 44"><circle cx="22" cy="22" r="20" fill="#e34096"/><circle cx="22" cy="22" r="16" stroke="#fff" stroke-width="2" fill="none"/></svg><span>Safety Auto shut-off</span></li>
    <li><svg viewBox="0 0 44 44"><circle cx="22" cy="22" r="20" fill="#e34096"/><circle cx="22" cy="22" r="16" stroke="#fff" stroke-width="2" fill="none"/></svg><span>Automatic moisture balance system</span></li>
    <li><svg viewBox="0 0 44 44"><circle cx="22" cy="22" r="20" fill="#e34096"/><circle cx="22" cy="22" r="16" stroke="#fff" stroke-width="2" fill="none"/></svg><span>Negative Ions Healthy Air</span></li>
    <li><svg viewBox="0 0 44 44"><circle cx="22" cy="22" r="20" fill="#e34096"/><circle cx="22" cy="22" r="16" stroke="#fff" stroke-width="2" fill="none"/></svg><span>Remote control &amp; touch panel</span></li>
    <li><svg viewBox="0 0 44 44"><circle cx="22" cy="22" r="20" fill="#e34096"/><circle cx="22" cy="22" r="16" stroke="#fff" stroke-width="2" fill="none"/></svg><span>Dual-Mist Outlets, 360 degree rotating</span></li>
    <li><svg viewBox="0 0 44 44"><circle cx="22" cy="22" r="20" fill="#e34096"/><circle cx="22" cy="22" r="16" stroke="#fff" stroke-width="2" fill="none"/></svg><span>Large capacity tank, run up to 12 hours</span></li>
  </ul>
</aside>

</body>
</html>
```